BOLD PINE HEATING AND COOLING

Industry/Entity Type

Hvac

Requirements
Must have
• logo
My name: Gavin Pruszynski
Phone number 555-309-4461
Text:
Furnace and AC repairs
New furnace and AC installation
Ductwork
Gas lines
Water Tanks
Tankless water heaters
Nice to have
• Profesional modern look

```html
<!DOCTYPE html>
<html lang="en">
<head>
<meta charset="utf-8">
<title>Bold Pine Heating and Cooling – Business Cards</title>
<link rel="stylesheet" href="https://fonts.googleapis.com/css2?family=Cinzel:wght@600&family=Montserrat:wght@400;500&display=swap">
<style>
  :root {
    --backdrop: #1b1b1c;
    --card: #2a2a2b;
    --card-edge: #242425;
    --brand-blue: #1f5fb8;
    --brand-red: #d9202e;
    --brand-green: #6cbf3c;
    --text-light: #f2f2f2;
  }
  * { box-sizing: border-box; margin: 0; padding: 0; }
  html, body {
    width: 1200px; height: 900px; overflow: hidden;
    background: var(--backdrop);
  }
  .sheet {
    width: 1200px; height: 900px;
    display: flex; flex-direction: column; align-items: center; justify-content: center;
    gap: 34px;
  }
  .card {
    position: relative;
    width: 720px; height: 400px;
    background: linear-gradient(135deg, var(--card) 0%, var(--card-edge) 100%);
    overflow: hidden;
  }
  .color-band {
    position: absolute; left: 0; right: 0; bottom: 0; height: 9px;
    display: flex;
  }
  .color-band span { flex: 1; }
  .color-band .blue { background: var(--brand-blue); }
  .color-band .red { background: var(--brand-red); }
  .color-band .green { background: var(--brand-green); }

  .brand {
    display: flex; align-items: center; gap: 14px;
  }
  .brand-dot {
    width: 22px; height: 22px; border-radius: 50%;
    background: var(--brand-blue); flex: none;
  }
  .brand-name {
    font-family: "Cinzel", serif; font-weight: 600;
    color: var(--brand-blue); line-height: 1.05;
  }

  /* Front */
  .card-front .brand {
    position: absolute; top: 96px; left: 0; right: 0; justify-content: center;
  }
  .card-front .brand-name { font-size: 40px; text-align: left; }
  .services {
    position: absolute; top: 262px; left: 0; right: 0;
    text-align: center;
    font-family: "Montserrat", sans-serif; font-size: 18px; line-height: 1.45;
    color: var(--text-light); letter-spacing: 0.3px;
  }
  .services .sep { color: var(--brand-green); padding: 0 6px; }

  /* Back */
  .card-back .brand {
    position: absolute; left: 48px; top: 140px; width: 300px;
  }
  .card-back .brand-name { font-size: 30px; }
  .divider {
    position: absolute; left: 372px; top: 92px; width: 2px; height: 186px;
    background: var(--brand-green);
  }
  .contact {
    position: absolute; left: 412px; top: 106px;
    font-family: "Montserrat", sans-serif; color: var(--text-light);
  }
  .contact-name {
    font-family: "Cinzel", serif; font-weight: 600; font-size: 24px;
    color: var(--brand-blue); letter-spacing: 0.5px;
  }
  .contact-role { font-size: 19px; margin-top: 2px; margin-bottom: 22px; }
  .contact-list { list-style: none; font-size: 20px; line-height: 1.5; }
  .contact-list li { display: flex; align-items: center; gap: 10px; }
  .contact-list svg { width: 14px; height: 14px; flex: none; }
</style>
</head>
<body>
<main class="sheet">

  <section class="card card-front">
    <div class="brand">
      <span class="brand-dot"></span>
      <div class="brand-name">Bold Pine<br>Heating and Cooling</div>
    </div>
    <p class="services">
      Furnace and AC repairs<span class="sep">|</span>New furnace and AC installation<br>
      Ductwork<span class="sep">|</span>Gas lines<span class="sep">|</span>Water Tanks<span class="sep">|</span>Tankless water heaters
    </p>
    <div class="color-band"><span class="blue"></span><span class="red"></span><span class="green"></span></div>
  </section>

  <section class="card card-back">
    <div class="brand">
      <span class="brand-dot"></span>
      <div class="brand-name">Bold Pine<br>Heating and Cooling</div>
    </div>
    <div class="divider"></div>
    <div class="contact">
      <p class="contact-name">Gavin Pruszynski</p>
      <p class="contact-role">Director</p>
      <ul class="contact-list">
        <li>
          <svg viewBox="0 0 16 16" aria-hidden="true"><path d="M4 1l3 3-2 2c1 2 3 4 5 5l2-2 3 3-2 3C7 15 1 9 1 3z" fill="#6cbf3c"/></svg>
          555-309-4461
        </li>
        <li>
          <svg viewBox="0 0 16 16" aria-hidden="true"><rect x="1.5" y="3.5" width="13" height="9" fill="none" stroke="#6cbf3c" stroke-width="1.5"/><path d="M1.5 3.5l6.5 5 6.5-5" fill="none" stroke="#6cbf3c" stroke-width="1.5"/></svg>
          info@boldpineheating.com
        </li>
        <li>
          <svg viewBox="0 0 16 16" aria-hidden="true"><circle cx="8" cy="8" r="6.5" fill="none" stroke="#6cbf3c" stroke-width="1.5"/><path d="M1.5 8h13M8 1.5c-3 3.5-3 9.5 0 13M8 1.5c3 3.5 3 9.5 0 13" fill="none" stroke="#6cbf3c" stroke-width="1.2"/></svg>
          www.boldpineheating.com
        </li>
      </ul>
    </div>
    <div class="color-band"><span class="blue"></span><span class="red"></span><span class="green"></span></div>
  </section>

</main>
</body>
</html>
```